Business Card Design Project

This is the first time we use our new logo. We need a business card that we can use both on our institutional corporate relationships and also that works for our staff that deals with consumers directly.

VELUNDA is a new company dedicated to empower consumers and to provide them with the best choices for specialized health care using the latest telemedicine technology (medicine at a distance via videoconference).

We want to print this cards in high quality materials and process. We will like designs that allow us to use UV spot varnish and other techniques that will differentiate us.

We are including Two different versions of Color logos. In addition we are including white over black background logos. Those can be used replacing the black for a color.

Please note this is the first time we will be creating any corporate materials with our new logo and colors.

Target Market(s)

34+ consumers of medium high and high socioeconomic levels.

Industry/Entity Type

Health

Requirements
Must have
• Our logo on its original colors
Should not have
• Any other graphical element or design that is not our logo

```html
<!DOCTYPE html>
<html lang="en">
<head>
<meta charset="utf-8">
<title>VELUNDA — Business Card Set</title>
<link rel="stylesheet" href="https://fonts.googleapis.com/css2?family=Jost:wght@400;500;600;700&display=swap">
<style>
  :root {
    --stage: #ecebe8;
    --label: #2a2a2a;
    --brand-blue: #1c5784;
    --brand-sky: #5ab6e2;
    --brand-mid: #2e86c6;
    --metal-light: #e4e4e4;
    --metal-mid: #c3c3c3;
    --metal-dark: #8e8e8e;
    --ink: #1f1f1f;
    --white: #ffffff;
    --muted: #3c3c3c;
  }
  * { margin: 0; padding: 0; box-sizing: border-box; }
  html, body {
    width: 1200px; height: 788px; overflow: hidden;
    background: var(--stage);
    font-family: "Jost", "Futura", sans-serif;
  }
  .sheet { position: relative; width: 1200px; height: 788px; }
  .view-label {
    position: absolute; width: 525px; text-align: center;
    font-size: 20px; font-weight: 400; color: var(--label);
  }
  .card {
    position: absolute; width: 525px; height: 300px;
    border-radius: 22px; overflow: hidden;
    box-shadow: 0 4px 12px rgba(0,0,0,0.25);
  }
  .card--front { left: 53px; top: 73px; }
  .card--back-white { left: 622px; top: 73px; background: var(--white); }
  .card--back-metal {
    left: 53px; top: 445px;
    background: linear-gradient(180deg, var(--metal-light) 0%, var(--metal-mid) 55%, var(--metal-dark) 100%);
  }
  .card--back-blue { left: 622px; top: 445px; background: var(--brand-blue); }

  .card-art { position: absolute; inset: 0; }

  .wordmark {
    position: absolute; font-weight: 600; letter-spacing: 2px; line-height: 1;
  }
  .mark-dot { position: absolute; border-radius: 50%; }

  .front-wordmark { left: 95px; top: 66px; font-size: 34px; color: var(--white); }
  .front-dot { left: 30px; top: 55px; width: 54px; height: 54px; border: 0; background: var(--white); }

  .holder { position: absolute; right: 25px; top: 102px; text-align: right; color: var(--brand-blue); }
  .holder-name { font-size: 17px; font-weight: 600; line-height: 1.2; }
  .holder-role { font-size: 13px; font-weight: 400; }

  .contact {
    position: absolute; right: 25px; top: 213px; text-align: right;
    font-size: 13px; color: var(--ink); line-height: 25px;
  }
  .contact b { font-style: italic; font-weight: 600; }

  .site {
    position: absolute; left: 0; right: 0; text-align: center;
    font-size: 15px; letter-spacing: 3.4px; font-weight: 400;
  }

  .b1-dot { left: 100px; top: 72px; width: 78px; height: 78px; background: var(--brand-mid); }
  .b1-wordmark { left: 193px; top: 125px; font-size: 50px; color: var(--brand-blue); }
  .b1-site { top: 258px; color: var(--muted); }

  .b2-dot { left: 100px; top: 95px; width: 80px; height: 80px; background: var(--brand-mid); }
  .b2-wordmark { left: 193px; top: 140px; font-size: 48px; color: var(--brand-blue); }
  .b2-site { top: 262px; color: var(--white); }

  .b3-dot { left: 222px; top: 36px; width: 80px; height: 80px; background: var(--brand-sky); }
  .b3-wordmark { left: 0; right: 0; text-align: center; top: 175px; font-size: 48px; color: var(--white); }
  .b3-site { top: 262px; color: var(--white); }
</style>
</head>
<body>
<main class="sheet">
  <p class="view-label" style="left:53px; top:34px;">Front</p>
  <p class="view-label" style="left:622px; top:34px;">Back - 1</p>
  <p class="view-label" style="left:53px; top:405px;">Back - 2</p>
  <p class="view-label" style="left:622px; top:405px;">Back - 3</p>

  <section class="card card--front" aria-label="Card front">
    <svg class="card-art" viewBox="0 0 525 300" width="525" height="300" aria-hidden="true">
      <defs>
        <linearGradient id="metal-front" x1="0" y1="0" x2="0" y2="1">
          <stop offset="0" stop-color="#e2e2e2"/>
          <stop offset="1" stop-color="#b9b9b9"/>
        </linearGradient>
      </defs>
      <rect width="525" height="300" fill="url(#metal-front)"/>
      <path d="M0 0 H525 V6 C390 30 190 130 18 300 H0 Z" fill="var(--brand-blue)"/>
      <path d="M525 14 C395 40 205 140 48 300 H26 C195 128 395 30 525 6 Z" fill="#d9d9d9"/>
      <path d="M525 16 C400 44 215 145 62 300 H40 C205 134 400 34 525 22 Z" fill="var(--brand-sky)"/>
    </svg>
    <span class="mark-dot front-dot"></span>
    <span class="wordmark front-wordmark">VELUNDA</span>
    <div class="holder">
      <p class="holder-name">Your Name</p>
      <p class="holder-role">Designation</p>
    </div>
    <div class="contact">
      <p><b>p</b> : +12 345 67890 &nbsp;|&nbsp; <b>f</b> : +12 345 67890</p>
      <p><b>e</b> : info@website.com &nbsp;|&nbsp; <b>w</b> : www.website.com</p>
      <p>#0000, Street Name, Area Name, Country Code</p>
    </div>
  </section>

  <section class="card card--back-white" aria-label="Card back, white">
    <span class="mark-dot b1-dot"></span>
    <span class="wordmark b1-wordmark">VELUNDA</span>
    <p class="site b1-site">www.website.com</p>
  </section>

  <section class="card card--back-metal" aria-label="Card back, brushed metal">
    <span class="mark-dot b2-dot"></span>
    <span class="wordmark b2-wordmark">VELUNDA</span>
    <p class="site b2-site">www.website.com</p>
  </section>

  <section class="card card--back-blue" aria-label="Card back, blue">
    <span class="mark-dot b3-dot"></span>
    <span class="wordmark b3-wordmark">VELUNDA</span>
    <p class="site b3-site">www.website.com</p>
  </section>
</main>
</body>
</html>
```